Medical centre needs a business card

We are a medcial centre in Australia, needing a new business card. Our demographic is low working class families. We are going to be renovating our premises to modernise the look and also had a new logo done a few months ago representing quality and community, and now need to update our cards. It needs to be doubled sided, with logo and contact details on the front, and appointment details on the back. . Needs to be modern and simple, easy to read. <br/><br/>Name: Kindle Grove Medical Centre <br/>Address: 512 Parmley Rd (Cnr Parmley Rd & Osgood Creek Rd),<br/>Tindarra Court Shopping Centre, Paralowie, SA 5108<br/>Ph: 08 8461 3072<br/>Tag line: Where your wellbeing comes first<br/>Website: www.kindlegrovemedicalcentre-example.com.au<br/>Online bookings also available<br/><br/>(On the back, to have 3 lines of appointments that can be written in.<br/>Day, date, time)<br/><br/>Your next appointment is on<br/>Can try “M T W Th F Sa Su _________________ at ____________ am/pm” or other combinations <br/>Please advise as soon as possible if unable to attend<br/>Cancellation fees apply if less than 2 hrs notice<br/>Online appointments available (please highlight this option by either by position, colour or font)

Target Market(s)

Lower social economic working class, young families to seniors

Industry/Entity Type

Medical Centre

Contact Information for Business Card

Kindle Grove Medical Centre
512 Parmley Rd (Cnr Parmley Rd & Osgood Creek Drive)
Tindarra Court Shopping Centre
Ashbury Vale SA 5190
Ph: 08 8461 3072
www.kindlegrovemedicalcentre-example.com.au
Tagline line: where your wellbeing comes first
Back side is for appointments
Your next appointment is with Dr ______________
Day/date/time (Please give 3 lines of appointments)
Please advise as soon as possible if unable to attend
Cancellation fees apply if less than 2 hours notice
Online appointments available
Book online easily and conveniently (please highlight online appointments)

Font styles to use
Serif
Sans Serif

Colors

Designer to choose colors to be used in the design.

Requirements
Must have
• Modern and simple
• Easy to ready
• Induces a wellbeing feeling
• Incorporate our logo colours and feel from logo
• Induces feeling of stability and security
Nice to have
• Attract attention
• Pleasant to look at
• Feeling of innovation
Should not have
• Loud clashing colours
• Overly luxurious feeling
• Overly artistic

```html
<!DOCTYPE html>
<html lang="en">
<head>
<meta charset="utf-8">
<title>Kindle Grove Medical Centre – Business Card</title>
<link rel="stylesheet" href="https://fonts.googleapis.com/css2?family=Josefin+Sans:wght@600;700&family=Work+Sans:wght@400;500&display=swap">
<style>
  :root {
    --brand-blue: #1570c2;
    --brand-green: #9acb3c;
    --text-grey: #7a7a7a;
    --card-white: #ffffff;
    --backdrop: #2b2b2b;
  }
  html, body {
    margin: 0;
    padding: 0;
    width: 1200px;
    height: 900px;
    overflow: hidden;
    background: var(--backdrop);
  }
  .canvas {
    position: relative;
    width: 1200px;
    height: 900px;
  }
  .card {
    position: absolute;
    left: 261px;
    width: 656px;
    height: 357px;
    background: var(--card-white);
    border-radius: 24px;
    overflow: hidden;
    box-shadow: 0 4px 14px rgba(0,0,0,0.35);
  }
  .card--front { top: 69px; }
  .card--back { top: 472px; }

  /* Front */
  .brand {
    position: absolute;
    left: 28px;
    top: 104px;
    display: flex;
    align-items: center;
    gap: 12px;
  }
  .brand__dot {
    width: 30px;
    height: 30px;
    border-radius: 50%;
    background: var(--brand-green);
  }
  .brand__name {
    font-family: "Josefin Sans", sans-serif;
    font-weight: 700;
    font-size: 25px;
    letter-spacing: 0.5px;
    color: var(--brand-blue);
    text-transform: uppercase;
    line-height: 1;
    padding-top: 4px;
  }
  .contact-icons {
    position: absolute;
    left: 28px;
    top: 198px;
    width: 628px;
    height: 26px;
  }
  .contact-details {
    position: absolute;
    left: 29px;
    top: 241px;
    font-family: "Josefin Sans", sans-serif;
    font-weight: 600;
    color: var(--brand-blue);
    text-transform: uppercase;
    letter-spacing: 1.6px;
    font-size: 16px;
    line-height: 23px;
  }
  .contact-details p { margin: 0; }
  .contact-details .website { font-size: 15px; letter-spacing: 1.2px; }
  .contact-details .address { margin-top: 11px; }

  /* Back */
  .tagline {
    position: absolute;
    left: 0;
    right: 0;
    top: 32px;
    margin: 0;
    text-align: center;
    font-family: "Josefin Sans", sans-serif;
    font-weight: 600;
    font-size: 24px;
    letter-spacing: 1px;
    color: var(--brand-blue);
    text-transform: uppercase;
  }
  .appointment {
    position: absolute;
    left: 105px;
    top: 100px;
    width: 436px;
    font-family: "Work Sans", sans-serif;
  }
  .appointment__doctor {
    margin: 0 0 22px;
    font-size: 16px;
    font-weight: 500;
    letter-spacing: 0.8px;
    color: var(--brand-blue);
    display: flex;
    align-items: baseline;
    width: 428px;
  }
  .appointment__field {
    margin: 0 0 21px;
    font-size: 16px;
    letter-spacing: 0.6px;
    color: var(--text-grey);
    display: flex;
    align-items: baseline;
    gap: 6px;
  }
  .blank {
    display: inline-block;
    flex: 1;
    border-bottom: 1px solid var(--text-grey);
    height: 1px;
    margin-left: 6px;
  }
  .notice {
    position: absolute;
    left: 0;
    right: 0;
    top: 276px;
    margin: 0;
    text-align: center;
    font-family: "Work Sans", sans-serif;
    font-size: 15.5px;
    letter-spacing: 1.1px;
    line-height: 20px;
    color: var(--text-grey);
  }
  .notice .online {
    color: var(--brand-green);
    font-weight: 500;
    font-size: 16px;
  }
</style>
</head>
<body>
<main class="canvas">

  <section class="card card--front" aria-label="Card front">
    <div class="brand">
      <span class="brand__dot"></span>
      <span class="brand__name">Kindle Grove Medical Centre</span>
    </div>

    <svg class="contact-icons" viewBox="0 0 628 26" aria-hidden="true">
      <g fill="none" stroke="#9acb3c" stroke-width="1.4">
        <circle cx="13" cy="13" r="12"/>
        <circle cx="46" cy="13" r="12"/>
        <circle cx="80" cy="13" r="12"/>
        <line x1="102" y1="13" x2="628" y2="13"/>
      </g>
      <path d="M9.5 7.5c1-.8 1.6-.6 2.1.6l.6 1.4c.3.7-.2 1.2-.8 1.6.5 1.5 1.3 2.6 2.5 3.6.6-.5 1.2-.8 1.8-.3l1.2.9c.8.6.7 1.3-.2 2.2-1.6 1.5-4.4-.5-6-3-1.5-2.4-2.3-5.8-1.2-7z" fill="#1570c2"/>
      <g fill="none" stroke="#1570c2" stroke-width="1">
        <circle cx="46" cy="13" r="7"/>
        <ellipse cx="46" cy="13" rx="3.2" ry="7"/>
        <line x1="39" y1="13" x2="53" y2="13"/>
        <line x1="40" y1="9.5" x2="52" y2="9.5"/>
        <line x1="40" y1="16.5" x2="52" y2="16.5"/>
      </g>
      <path d="M80 21c-3-4-5-6.5-5-9a5 5 0 0 1 10 0c0 2.5-2 5-5 9z" fill="#1570c2"/>
      <circle cx="80" cy="11.8" r="1.7" fill="#ffffff"/>
    </svg>

    <div class="contact-details">
      <p class="phone">08 8461 3072</p>
      <p class="website">www.kindlegrovemedicalcentre-example.com.au</p>
      <div class="address">
        <p>512 Parmley Rd (Cnr Parmley Rd &amp; Osgood Creek Drive)</p>
        <p>Tindarra Court Shopping Centre Ashbury Vale SA 5190</p>
      </div>
    </div>
  </section>

  <section class="card card--back" aria-label="Card back">
    <h2 class="tagline">Where your wellbeing comes first</h2>

    <div class="appointment">
      <p class="appointment__doctor">Your next appointment is with Dr <span class="blank"></span></p>
      <p class="appointment__field">Day <span class="blank"></span></p>
      <p class="appointment__field">date <span class="blank"></span></p>
      <p class="appointment__field">time <span class="blank"></span></p>
    </div>

    <p class="notice">
      Please advise as soon as possible if unable to attend<br>
      Cancellation fees apply if less than 2 hours notice<br>
      <span class="online">Online appointments available.</span>
    </p>
  </section>

</main>
</body>
</html>
```